Powerpoint design template for LUMOTEX for new digital platform

We would like to use a PowerPoint template, we would like to create a new page, we would like to create a new digital platform LUMOTEX for schools and parents for the creation of playful communication and educational tools for children to enhance their positive development, amaze them learn in a playful way. This platform is going to be the most creative, stimulating and innovative classroom, easy to use and fast to implement. Scrapbooking, collages ... Magazine, newsletters Diplomla / awards Slideshows Facebook Calendars Organizers Greetings Games ... This powerpoint template will be used essential to We are looking for a professional design, positioning our brand in the children market with an adult hearing. so you will need to find a good deal. Primary target: nurseries & schools from 0 to 18 years old and universities (in 2nd phase) Secondary target: small & medium businesses Third target: general public, and TPE If it is a color scheme, then it is suggested that it be marketed in Europe (UK, Italy, Spain) and in a 2nd Stage USA and other countries. multiple options for front page, insidious pages (multiple styles with limited text and extended text) and final contact page We need something to read, we can not do it too much, but we can not do it. , and inside pages aligned to our logo

Target Market(s)

Target 1; Education with teacher Target 2; parents and grandparents

Industry/Entity Type

Education

Font styles to use
Other font styles liked:
• not decided. but not too fancy

Requirements
Must have
• Multi page options for front page, page insides (multiple styles with limited text and extended text) and final page contact
Nice to have
• do not have a lot of ideas. We need something to read, we can not get away from it
Should not have
• not too fancy and busy: keep clarity & simplicity while reassuring on quality

```html
<!DOCTYPE html>
<html lang="en">
<head>
<meta charset="utf-8">
<title>LUMOTEX – Presentation Template Pages</title>
<link href="https://fonts.googleapis.com/css2?family=Roboto+Condensed:wght@400;700&family=Open+Sans:wght@400;600&display=swap" rel="stylesheet">
<style>
  :root{
    --board:#000000;
    --lime:#c6dc2b;
    --lime-deep:#a8c418;
    --lime-pale:#dde97a;
    --orange:#f29a1f;
    --orange-deep:#e98a12;
    --panel-yellow:#f6fa8c;
    --cream:#fdfbd6;
    --ink:#1d1d1d;
    --ink-soft:#4a4a4a;
    --cyan:#1eaec6;
    --pink:#e8368a;
    --accent-orange:#f7941d;
    --white:#ffffff;
    --grid:#e3eef2;
  }
  *{box-sizing:border-box;margin:0;padding:0}
  html,body{width:806px;height:1200px;overflow:hidden;background:var(--board)}
  .board{position:relative;width:806px;height:1200px;background:var(--board)}
  .slide{position:absolute;width:385px;height:288px;overflow:hidden;background:var(--white);
    font-family:"Roboto Condensed",Arial,sans-serif;color:var(--ink)}
  .col-a{left:10px}.col-b{left:405px}
  .row-1{top:9px}.row-2{top:308px}.row-3{top:605px}.row-4{top:902px}
  .abs{position:absolute}
  .shape{position:absolute;left:0;top:0;width:385px;height:288px}

  /* brand */
  .brand{position:absolute;display:flex;align-items:center;gap:4px;
    font-family:"Roboto Condensed",Arial,sans-serif;font-weight:700;color:var(--ink);letter-spacing:.5px}
  .brand .mark{display:block;background:var(--lime)}
  .brand-sm{font-size:12px}
  .brand-sm .mark{width:9px;height:9px}
  .brand-lg{font-size:30px}
  .brand-lg .mark{width:22px;height:22px}
  .tagline{position:absolute;font-size:6.5px;letter-spacing:2px;color:var(--ink-soft);line-height:1.25}

  /* titles */
  .project-title{font-weight:700;font-size:17px;letter-spacing:.2px;color:var(--ink)}
  .project-title .hi{color:var(--cyan)}
  .subtext{font-size:10.5px;color:var(--ink)}
  .bar-title{position:absolute;left:10px;top:7px;font-weight:700;font-size:15px;color:var(--ink)}

  .media{position:absolute}

  /* footers */
  .footer-url{position:absolute;left:8px;bottom:8px;font-size:7px;color:var(--ink)}
  .footer-page{position:absolute;right:8px;bottom:8px;font-size:7px;color:var(--ink)}

  /* orange side-strip page */
  .s2-head{position:absolute;left:111px;top:14px;font-family:"Open Sans",Arial,sans-serif;
    font-weight:600;font-size:10.5px;color:var(--white)}
  .s2-panel{position:absolute;left:111px;top:33px;width:271px;height:246px;background:var(--panel-yellow);
    padding:29px 18px 0 15px;font-family:"Open Sans",Arial,sans-serif}
  .s2-item{height:58px}
  .s2-item h3{font-size:9px;font-weight:600;color:var(--ink);line-height:1.2}
  .s2-item p{font-size:7.3px;line-height:1.45;color:var(--ink-soft)}

  /* three topics page */
  .topic-list{position:absolute;left:12px;top:55px;width:350px}
  .topic{display:flex;gap:6px;height:63px}
  .topic:nth-child(2){height:75px}
  .topic svg{flex:none;margin-top:-1px}
  .topic h3{font-size:9px;font-weight:700;color:var(--accent-orange);margin-bottom:3px}
  .topic p{font-size:6.3px;line-height:1.85;color:var(--ink)}

  /* extended text with photo */
  .s5-copy{position:absolute;left:16px;top:47px;width:205px}
  .s5-copy h3{font-size:13px;font-weight:700;color:var(--pink);margin-bottom:2px}
  .s5-copy p{font-size:6.9px;line-height:13.4px;color:var(--ink)}

  /* illustrated banner list */
  .s7-list{position:absolute;left:20px;top:146px;width:350px;font-family:"Open Sans",Arial,sans-serif}
  .s7-item{display:flex;gap:16px;height:47px}
  .s7-item .book{flex:none;width:13px;height:15px;margin-top:4px;border-radius:2px}
  .s7-item h3{font-size:8.5px;font-weight:400;color:var(--accent-orange);line-height:1.3}
  .s7-item p{font-size:7.6px;line-height:1.5;color:var(--ink-soft)}
  .s7-item:nth-child(2) h3{color:var(--pink)}
  .s7-item:nth-child(3) h3{color:var(--cyan)}

  /* numbered list on grid paper */
  .grid-paper{background-color:var(--white);
    background-image:repeating-linear-gradient(0deg,var(--grid) 0 1px,transparent 1px 16px),
      repeating-linear-gradient(90deg,var(--grid) 0 1px,transparent 1px 16px)}
  .s8-title{position:absolute;left:15px;top:10px;font-family:"Open Sans",Arial,sans-serif;font-weight:600;
    font-size:14px;letter-spacing:.6px;color:var(--cyan)}
  .s8-list{position:absolute;left:24px;top:47px;width:340px;font-family:"Open Sans",Arial,sans-serif}
  .s8-item{display:flex;gap:11px;height:53px}
  .num{flex:none;width:18px;height:18px;border-radius:50%;display:flex;align-items:center;justify-content:center;
    font-size:8.5px;font-weight:600;color:var(--ink);background:var(--white);margin-top:1px}
  .num-1{border:3px solid var(--accent-orange);background:#ffc629}
  .num-2{border:3px solid var(--pink)}
  .s8-item p{font-size:8.6px;line-height:1.55;color:var(--ink-soft);width:305px}
</style>
</head>
<body>
<main class="board">

  <!-- Cover with photo -->
  <section class="slide col-a row-1 cover-photo">
    <div class="media" role="img" aria-label="Photo of three cheerful children leaning over a white board"
      style="left:0;top:0;width:385px;height:215px;background:linear-gradient(180deg,#fafafa 0%,#f0e6dc 45%,#f4f4f4 100%)"></div>
    <svg class="shape" viewBox="0 0 385 288" aria-hidden="true">
      <polygon points="0,218 260,218 204,288 0,288" fill="var(--lime)"/>
      <polygon points="230,218 260,218 204,288 178,288" fill="var(--lime-deep)"/>
    </svg>
    <div class="abs project-title" style="left:14px;top:240px">PROJECT <span class="hi">TITLE HERE</span></div>
    <div class="abs subtext" style="left:14px;top:263px">SUBTEXT HERE</div>
    <div class="brand brand-lg" style="left:262px;top:240px;font-size:24px"><span class="mark" style="width:14px;height:14px"></span>LUMOTEX</div>
    <div class="tagline" style="left:280px;top:271px">YOUR TAGLINE<br>GOES HERE</div>
  </section>

  <!-- Orange content page with side illustration -->
  <section class="slide col-b row-1 side-strip" style="background:var(--orange)">
    <div class="media" role="img" aria-label="Illustrated strip of cartoon children stacked down the left edge"
      style="left:0;top:0;width:111px;height:288px;background:linear-gradient(90deg,#fff3c9 0%,#fbd48a 60%,#f4a93a 100%)"></div>
    <div class="s2-head">Cotnent TItele Here</div>
    <div class="brand brand-sm" style="right:12px;top:12px"><span class="mark"></span>LUMOTEX</div>
    <div class="s2-panel">
      <div class="s2-item"><h3>Subtext here</h3><p>Lemon drops oat cake oat cake sugar plum sweet gingerbread chocolate cake gingerbread. Lemon drops oat cake oat cake sugar plum sweet</p></div>
      <div class="s2-item"><h3>Subtext here</h3><p>Lemon drops oat cake oat cake sugar plum sweet gingerbread chocolate cake gingerbread. Lemon drops oat cake oat cake sugar plum sweet</p></div>
      <div class="s2-item"><h3>Subtext here</h3><p>Lemon drops oat cake oat cake sugar plum sweet gingerbread chocolate cake gingerbread. Lemon drops oat cake oat cake sugar plum sweet</p></div>
    </div>
  </section>

  <!-- Cover, diagonal -->
  <section class="slide col-a row-2 cover-diagonal">
    <svg class="shape" viewBox="0 0 385 288" aria-hidden="true">
      <polygon points="0,0 372,0 100,288 0,288" fill="var(--lime)"/>
      <polygon points="360,0 385,0 385,8 112,288 100,288" fill="var(--lime-pale)"/>
      <polygon points="372,0 385,0 385,4 108,288 100,288" fill="var(--lime-deep)" opacity=".5"/>
    </svg>
    <div class="abs project-title" style="left:33px;top:92px;font-size:19px">PROJECT <span class="hi">TITLE HERE</span></div>
    <div class="abs subtext" style="left:33px;top:118px;font-size:11.5px">SUBTEXT HERE</div>
    <div class="brand brand-lg" style="left:224px;top:204px"><span class="mark"></span>LUMOTEX</div>
    <div class="tagline" style="left:230px;top:245px;font-size:7px">YOUR TAGLINE<br>GOES HERE</div>
  </section>

  <!-- Three topics page -->
  <section class="slide col-b row-2 topics">
    <svg class="shape" viewBox="0 0 385 288" aria-hidden="true">
      <polygon points="0,0 332,0 314,32 0,32" fill="var(--lime)"/>
      <polygon points="332,0 345,0 327,32 314,32" fill="var(--lime-pale)"/>
      <polygon points="0,262 150,262 130,288 0,288" fill="var(--lime)"/>
      <polygon points="150,262 385,262 385,288 130,288" fill="var(--orange)"/>
    </svg>
    <div class="bar-title">PROJECT TITLE HERE</div>
    <div class="brand brand-sm" style="right:10px;top:10px"><span class="mark"></span>LUMOTEX</div>
    <div class="topic-list">
      <div class="topic">
        <svg width="18" height="18" viewBox="0 0 18 18" aria-hidden="true"><polygon points="9,1 11,7 17,7 12,11 14,17 9,13 4,17 6,11 1,7 7,7" fill="var(--accent-orange)"/></svg>
        <div><h3>SUBTEXT HERE</h3><p>Toffee caramels candy canes bonbon bonbon soufflé bonbon wafer. Topping I love halvah I love. Jujubes lemon drops I love jelly pie chocolate bar. Biscuit oat cake carrot cake. Muffin jelly beans chocolate chocolate. Sugar plum I love cheesecake marshmallow cream cake sweet cookies topping jelly gummies.</p></div>
      </div>
      <div class="topic">
        <svg width="18" height="18" viewBox="0 0 18 18" aria-hidden="true"><polygon points="9,1 11,7 17,7 12,11 14,17 9,13 4,17 6,11 1,7 7,7" fill="var(--accent-orange)"/></svg>
        <div><h3>SUBTEXT HERE</h3><p>Toffee caramels candy canes bonbon bonbon soufflé bonbon wafer. Topping I love halvah I love. Jujubes lemon drops I love jelly pie chocolate bar. Biscuit oat cake carrot cake. Muffin jelly beans chocolate chocolate. Sugar plum I love cheesecake marshmallow cream cake sweet cookies topping jelly gummies.</p></div>
      </div>
      <div class="topic">
        <svg width="18" height="18" viewBox="0 0 18 18" aria-hidden="true"><polygon points="9,1 11,7 17,7 12,11 14,17 9,13 4,17 6,11 1,7 7,7" fill="var(--accent-orange)"/></svg>
        <div><h3>SUBTEXT HERE</h3><p>Toffee caramels candy canes bonbon bonbon soufflé bonbon wafer. Topping I love halvah I love. Jujubes lemon drops I love jelly pie chocolate bar. Biscuit oat cake carrot cake. Muffin jelly beans chocolate chocolate. Sugar plum I love cheesecake marshmallow cream cake sweet cookies topping jelly gummies.</p></div>
      </div>
    </div>
    <div class="footer-url">www.lumotex.com</div>
    <div class="footer-page">Page : 01</div>
  </section>

  <!-- Extended text with photo -->
  <section class="slide col-a row-3 text-photo">
    <svg class="shape" viewBox="0 0 385 288" aria-hidden="true">
      <defs>
        <linearGradient id="paint-photo" x1="0" y1="0" x2="1" y2="1">
          <stop offset="0" stop-color="#f2c9a8"/>
          <stop offset=".45" stop-color="#e8b24a"/>
          <stop offset=".75" stop-color="#5db7d8"/>
          <stop offset="1" stop-color="#e9a27a"/>
        </linearGradient>
      </defs>
      <polygon points="0,0 340,0 80,288 0,288" fill="var(--lime)"/>
      <polygon points="340,0 352,0 92,288 80,288" fill="var(--lime-pale)"/>
      <polygon points="330,45 385,45 385,288 110,288" fill="url(#paint-photo)" role="img" aria-label="Photo of a child's hand covered in bright rainbow paint"/>
      <polygon points="0,268 150,268 132,288 0,288" fill="var(--lime)"/>
      <polygon points="150,262 385,262 385,288 128,288" fill="var(--orange)"/>
    </svg>
    <div class="brand brand-sm" style="right:10px;top:12px"><span class="mark"></span>LUMOTEX</div>
    <div class="s5-copy">
      <h3>SUBTEXT HERE</h3>
      <p>Toffee caramels candy canes bonbon bonbon soufflé bonbon wafer. Topping I love halvah I love. Jujubes lemon drops I love jelly pie chocolate bar. Biscuit oat cake carrot cake. Muffin jelly beans chocolate chocolate. Sugar plum I love cheesecake marshmallow cream cake sweet cookies topping jelly gummies. Toffee caramels candy canes bonbon bonbon soufflé bonbon wafer. Topping I love halvah I love. Jujubes lemon drops I love jelly pie chocolate bar. Biscuit oat cake carrot cake. Muffin jelly beans chocolate chocolate. Sugar plum I love cheesecake marshmallow cream cake sweet cookies topping jelly gummies.</p>
    </div>
    <div class="footer-url">www.lumotex.com</div>
    <div class="footer-page">Page : 01</div>
  </section>

  <!-- Blank content page -->
  <section class="slide col-b row-3 blank-page">
    <svg class="shape" viewBox="0 0 385 288" aria-hidden="true">
      <polygon points="0,0 332,0 314,38 0,38" fill="var(--lime)"/>
      <polygon points="332,0 345,0 327,38 314,38" fill="var(--lime-pale)"/>
      <rect x="0" y="275" width="385" height="13" fill="var(--orange)"/>
    </svg>
    <div class="bar-title" style="top:10px">PROJECT TITLE HERE</div>
    <div class="brand brand-sm" style="right:10px;top:13px"><span class="mark"></span>LUMOTEX</div>
  </section>

  <!-- Illustrated banner list -->
  <section class="slide col-a row-4 banner-list" style="background:var(--cream)">
    <div class="media" role="img" aria-label="Illustrated row of cartoon children holding books and pencils"
      style="left:0;top:30px;width:385px;height:88px;background:linear-gradient(180deg,#fffef4 0%,#fde9b8 55%,#f4c37a 100%)"></div>
    <div class="abs" style="left:0;top:118px;width:385px;height:3px;background:var(--orange-deep)"></div>
    <div class="brand brand-sm" style="right:10px;top:10px"><span class="mark"></span>LUMOTEX</div>
    <div class="s7-list">
      <div class="s7-item"><span class="book" style="background:#7a4aa0"></span><div><h3>Subtext here</h3><p>Lemon drops oat cake oat cake sugar plum sweet gingerbread chocolate cake gingerbread. Lemon drops oat cake oat cake sugar plum sweet</p></div></div>
      <div class="s7-item"><span class="book" style="background:var(--pink)"></span><div><h3>Subtext here</h3><p>Lemon drops oat cake oat cake sugar plum sweet gingerbread chocolate cake gingerbread. Lemon drops oat cake oat cake sugar plum sweet</p></div></div>
      <div class="s7-item"><span class="book" style="background:#1f8f8a"></span><div><h3>Subtext here</h3><p>Lemon drops oat cake oat cake sugar plum sweet gingerbread chocolate cake gingerbread. Lemon drops oat cake oat cake sugar plum sweet</p></div></div>
    </div>
  </section>

  <!-- Numbered list on grid paper -->
  <section class="slide col-b row-4 numbered grid-paper">
    <div class="s8-title">CONTENT TITLE HERE</div>
    <div class="brand brand-sm" style="right:10px;top:12px"><span class="mark"></span>LUMOTEX</div>
    <div class="s8-list">
      <div class="s8-item"><span class="num num-1">1</span><p>Lemon drops oat cake oat cake sugar plum sweet gingerbread chocolate cake gingerbread. Lemon drops oat cake oat cake sugar plum sweet</p></div>
      <div class="s8-item"><span class="num num-2">2</span><p>Lemon drops oat cake oat cake sugar plum sweet gingerbread chocolate cake gingerbread. Lemon drops oat cake oat cake sugar plum sweet</p></div>
    </div>
    <div class="media" role="img" aria-label="Illustration of cheerful cartoon food characters in a park with trees and a yellow balloon"
      style="left:0;top:160px;width:385px;height:128px;background:linear-gradient(180deg,rgba(255,255,255,0) 0%,#e8f4f8 35%,#cfe8a0 75%,#9ccc4a 100%)"></div>
  </section>

</main>
</body>
</html>
```